Business Card and Letterhead for Pimlu - modern real estate business

I need a double sided business card design for Pimlu. Please see business card brief here https://files.trelvonadocs.com/sheet/r/7QzTmWbaXLJnoPEd-kRyUgFhHsstbvCe2qfoMxDa_pz/view?mode=shared

Please feel free to design the business cards however you feel best. I am happy to give some creative freedoms and then provide feedback from there.

Please then also create a letterhead to match the business card design

Colors

Designer to choose colors to be used in the design.

Requirements
Must have
• Must be a modern, elegant business card which looks very professional

```html
<!DOCTYPE html>
<html lang="en">
<head>
<meta charset="utf-8">
<title>Pimlu – Business Card</title>
<link rel="stylesheet" href="https://fonts.googleapis.com/css2?family=Roboto:wght@400;500;700;900&family=Michroma&display=swap">
<style>
  :root {
    --stage: #2a2a2a;
    --ink: #111111;
    --card-white: #fbfbfb;
    --brand-red: #e01f26;
    --card-black: #000000;
    --photo-top: #d9d6d2;
    --photo-mid: #3a3b3f;
    --photo-low: #1e1f22;
  }
  * { box-sizing: border-box; margin: 0; padding: 0; }
  html, body { width: 1200px; height: 865px; overflow: hidden; }
  body {
    background: var(--stage);
    font-family: "Roboto", Arial, sans-serif;
    position: relative;
  }
  .card {
    position: absolute;
    left: 330px;
    width: 540px;
    height: 330px;
    border-radius: 18px;
    overflow: hidden;
    box-shadow: 0 10px 28px rgba(0,0,0,.45);
  }

  /* Back side */
  .card--back { top: 55px; background: var(--card-black); display: flex; align-items: center; justify-content: center; }
  .card--back .wordmark {
    color: var(--brand-red);
    font-weight: 900;
    font-size: 118px;
    letter-spacing: 6px;
    line-height: 1;
  }

  /* Front side */
  .card--front { top: 480px; background: var(--card-white); }
  .agent-photo {
    position: absolute;
    left: 318px; top: 40px;
    width: 200px; height: 290px;
    border-radius: 90px 90px 0 0;
    background: linear-gradient(180deg, var(--photo-top) 0%, var(--photo-top) 32%, var(--photo-mid) 40%, var(--photo-low) 100%);
  }
  .swoosh { position: absolute; inset: 0; width: 540px; height: 330px; }
  .front-wordmark {
    position: absolute; left: 34px; top: 30px;
    color: var(--brand-red);
    font-weight: 900;
    font-size: 60px;
    letter-spacing: 3px;
    line-height: 1;
  }
  .agent-id {
    position: absolute; left: 34px; top: 108px;
    padding-left: 14px;
    border-left: 6px solid var(--brand-red);
  }
  .agent-name {
    font-family: "Michroma", "Roboto", sans-serif;
    color: var(--brand-red);
    font-size: 20px;
    letter-spacing: 1px;
    line-height: 1.15;
  }
  .agent-title { color: var(--ink); font-size: 14px; font-weight: 500; margin-top: 2px; }
  .postal {
    position: absolute; left: 54px; top: 170px;
    color: var(--ink); font-size: 14px; font-weight: 500; line-height: 1.3;
  }
  .contacts {
    position: absolute; left: 54px; top: 212px;
    list-style: none;
    color: var(--ink); font-size: 14px; font-weight: 500;
  }
  .contacts li { display: flex; align-items: center; gap: 7px; height: 19px; }
  .contacts svg { width: 15px; height: 15px; flex: none; }
  .contacts .accent { color: var(--brand-red); }
  .licence {
    position: absolute; left: 362px; top: 282px;
    color: #ffffff; font-size: 13px; font-weight: 500;
    line-height: 1;
    white-space: nowrap;
    transform: rotate(-20deg);
    transform-origin: left center;
    letter-spacing: .5px;
  }
</style>
</head>
<body>

  <section class="card card--back" aria-label="Business card back">
    <span class="wordmark">PIMLU</span>
  </section>

  <section class="card card--front" aria-label="Business card front">
    <div class="agent-photo" role="img" aria-label="Portrait photo of the agent in a dark suit"></div>

    <svg class="swoosh" viewBox="0 0 540 330" aria-hidden="true">
      <path d="M110,330 C260,305 430,250 540,128 L540,146 C440,255 290,312 150,330 Z" fill="var(--ink)"/>
      <path d="M150,330 C295,312 445,258 540,150 L540,330 Z" fill="var(--brand-red)"/>
    </svg>

    <div class="front-wordmark">PIMLU</div>

    <div class="agent-id">
      <div class="agent-name">MARA DELLING</div>
      <div class="agent-title">Licenced Real Estate Agent</div>
    </div>

    <div class="postal">
      PO Box 731<br>Brackley Vale NSW 2790
    </div>

    <ul class="contacts">
      <li>
        <svg viewBox="0 0 16 16"><circle cx="8" cy="8" r="8" fill="var(--ink)"/><rect x="5.5" y="3.5" width="5" height="9" rx="1" fill="none" stroke="#fff" stroke-width="1.2"/></svg>
        0491 570 318
      </li>
      <li>
        <svg viewBox="0 0 16 16"><circle cx="8" cy="8" r="8" fill="var(--ink)"/><path d="M5 4.5 L6.8 4.5 L7.4 6.6 L6.3 7.4 C6.8 8.6 7.6 9.4 8.7 9.8 L9.5 8.7 L11.5 9.3 L11.5 11 C8 11.3 4.8 8.2 5 4.5 Z" fill="#fff"/></svg>
        1300 654 210
      </li>
      <li>
        <svg viewBox="0 0 16 16"><circle cx="8" cy="8" r="8" fill="var(--ink)"/><rect x="4" y="5" width="8" height="6" fill="none" stroke="#fff" stroke-width="1.1"/><path d="M4 5 L8 8.4 L12 5" fill="none" stroke="#fff" stroke-width="1.1"/></svg>
        mara@pimlu.com
      </li>
      <li>
        <svg viewBox="0 0 16 16"><circle cx="8" cy="8" r="8" fill="var(--ink)"/><circle cx="8" cy="8" r="4" fill="none" stroke="#fff" stroke-width="1.1"/><path d="M4 8 H12 M8 4 C6 6 6 10 8 12 M8 4 C10 6 10 10 8 12" fill="none" stroke="#fff" stroke-width=".9"/></svg>
        <span>www.<span class="accent">pimlu</span>.com</span>
      </li>
    </ul>

    <div class="licence">Lic No. 30418826</div>
  </section>

</body>
</html>
```